Packaging Design for Vanta Prime

We require an outstanding packaging design for our Vanta Prime brand, which offers hydration electrolyte supplements specifically tailored for athletes and sporty individuals.

Benchmark packaging design from quellix competitor attached. The product packaging contains 20 x 20g sticks of the product.

Target Market

Psychographic: Health-conscious, active lifestyle, values quality, functionality and sustainability.

product description 1:
HYDRATION BOOSTER
Refresh, Replenish, Recharge!

product description 2:
PREMIUM ISOTONIC ELECTROLYTE DRINK
Nutritional Expertise Since 1992.

Existing Logo: to add "since 1992"

Appeal to Target Market: Create a design that resonates with both men and women in the 25-55 age group.

Grafik Design: Develop a visually striking design that grabs attention in online retail environments like Brindleport.

Visuals: glass of water (or symbolic) and sticks (powder) just like benchmark brand quellix.

Design Elements
Use colours that are inside the Vanta-Prime Logo, attached.
Product will be available in 3 flavours. Lemon=yellow, Orange=orange, Black Currant=purple

Typography: Utilize strong, clean, and modern fonts. Ensure readability and create a sense of strength, endurance and reliability.

The product will be available in 3 flavours: Lemon, Orange and Johannisbeere

We look forward to seeing your creative ideas and innovative designs for our Vanta Prime brand packaging.

```html
<!DOCTYPE html>
<html lang="en">
<head>
<meta charset="utf-8">
<title>Vanta Prime Hydration Booster Packaging</title>
<link rel="stylesheet" href="https://fonts.googleapis.com/css2?family=Poppins:wght@600;700;800&family=Oswald:wght@400;500&display=swap">
<style>
:root{
  --bg:#dedede;
  --brand-blue:#233f8e;
  --brand-yellow:#fff200;
  --white:#ffffff;
  --lemon-main:#72be44;
  --lemon-dark:#066b35;
  --lemon-accent:#fff200;
  --currant-main:#9a2686;
  --currant-dark:#3d1a55;
  --currant-accent:#d6168b;
  --orange-main:#f79c29;
  --orange-dark:#ef4123;
  --orange-accent:#ffc20e;
}
*{box-sizing:border-box;margin:0;padding:0}
html,body{width:1200px;height:600px;overflow:hidden;background:var(--bg)}
.canvas{position:relative;width:1200px;height:600px}

.flavor-lemon{--main:var(--lemon-main);--dark:var(--lemon-dark);--accent:var(--lemon-accent);--tag-text:var(--lemon-dark);--fruit-a:#fff36b;--fruit-b:#e3c514;--leaf:#3f7a2a}
.flavor-currant{--main:var(--currant-main);--dark:var(--currant-dark);--accent:var(--currant-accent);--tag-text:var(--currant-dark);--fruit-a:#3a3550;--fruit-b:#0f0c1a;--leaf:#3f7a2a}
.flavor-orange{--main:var(--orange-main);--dark:var(--orange-dark);--accent:var(--orange-accent);--tag-text:var(--orange-dark);--fruit-a:#ffb640;--fruit-b:#f07a12;--leaf:#3f7a2a}

/* Carton front */
.carton{position:absolute;top:69px;width:327px;height:365px;background:var(--main);overflow:hidden}
.carton-sky{position:absolute;left:0;top:0}
.brand{position:absolute;left:78px;top:22px;font-family:'Poppins',sans-serif;font-weight:800;color:var(--brand-yellow);font-size:33px;line-height:.92;letter-spacing:-.5px}
.brand-since{position:absolute;left:210px;top:84px;font-family:'Poppins',sans-serif;font-weight:600;font-size:7px;color:var(--white)}
.portion{position:absolute;left:180px;top:122px;text-align:right;color:var(--white);font-family:'Oswald',sans-serif;line-height:1.1}
.portion-main{font-size:10px}
.portion-sub{font-size:6.5px}
.glass-icon{position:absolute;left:234px;top:100px}
.count-badge{position:absolute;left:264px;top:84px;width:34px;height:59px;background:var(--dark);color:var(--white);text-align:center;border-radius:0 0 2px 2px}
.count-num{font-family:'Oswald',sans-serif;font-weight:500;font-size:32px;line-height:1;display:block;margin-top:10px}
.count-label{font-family:'Poppins',sans-serif;font-weight:600;font-size:7px;display:block;margin-top:3px}
.headline{position:absolute;left:30px;top:160px;font-family:'Poppins',sans-serif;font-weight:700;color:var(--white);font-size:25.5px;letter-spacing:-.2px;line-height:1;white-space:nowrap}
.tagline{position:absolute;left:30px;top:193px;font-family:'Poppins',sans-serif;font-weight:600;color:var(--white);font-size:10.5px;white-space:nowrap}
.descriptor{position:absolute;left:30px;top:216px;font-family:'Poppins',sans-serif;font-weight:700;color:var(--tag-text);font-size:11px;white-space:nowrap;letter-spacing:-.1px}
.flavor-currant .descriptor{color:var(--currant-dark)}
.benefits{position:absolute;left:30px;top:244px;width:158px;height:72px;border:1.2px solid var(--tag-text);border-radius:7px;display:grid;grid-template-columns:82px 1fr;grid-template-rows:1fr 1fr;padding:6px 8px;color:var(--tag-text);font-family:'Oswald',sans-serif;font-size:8.5px;line-height:1.05;align-items:center}
.benefit{display:flex;align-items:center;gap:4px}
.benefit-big{font-family:'Poppins',sans-serif;font-weight:700;font-size:18px;line-height:1}
.fruit-visual{position:absolute;left:192px;top:244px;width:112px;height:72px;border-radius:50%;background:radial-gradient(circle at 60% 45%,var(--fruit-a),var(--fruit-b) 70%,transparent 72%)}
.flavor-band{position:absolute;left:0;top:310px}
.flavor-name{position:absolute;left:220px;width:100px;text-align:center;top:318px;font-family:'Poppins',sans-serif;font-weight:700;font-size:10px;letter-spacing:.6px;color:var(--tag-text)}
.footer-band{position:absolute;left:0;top:336px;width:100%;height:29px;background:var(--dark);display:flex;justify-content:space-between;align-items:center;padding:0 30px 0 32px;color:var(--white);font-family:'Oswald',sans-serif;font-size:10px;letter-spacing:.3px}

/* Stick sachet */
.stick{position:absolute;top:463px;width:279px;height:67px;background:var(--main);overflow:hidden}
.stick-edge{position:absolute;left:0;top:0;width:27px;height:100%;background:var(--accent);display:flex;justify-content:center;align-items:center;gap:3px}
.stick-edge span{writing-mode:vertical-rl;color:var(--tag-text);white-space:nowrap}
.stick-flavor{font-family:'Poppins',sans-serif;font-weight:700;font-size:6px}
.stick-weight{font-family:'Oswald',sans-serif;font-size:4.5px}
.stick-fruit{position:absolute;left:28px;top:6px;width:36px;height:56px;border-radius:45%;background:radial-gradient(circle at 50% 55%,var(--fruit-a),var(--fruit-b) 68%,transparent 71%)}
.stick-headline{position:absolute;left:62px;top:12px;font-family:'Poppins',sans-serif;font-weight:700;color:var(--white);font-size:13.5px;white-space:nowrap}
.stick-descriptor{position:absolute;left:62px;top:31px;font-family:'Poppins',sans-serif;font-weight:700;color:var(--tag-text);font-size:7.2px;white-space:nowrap}
.flavor-currant .stick-descriptor{color:var(--currant-dark)}
.stick-benefits{position:absolute;left:62px;top:43px;width:149px;height:24px;background:var(--dark);border-radius:5px 5px 0 0;display:flex;align-items:center;justify-content:space-around;padding:0 5px;color:var(--white);font-family:'Oswald',sans-serif;font-size:4px;line-height:1.05}
.stick-benefits .benefit{gap:2px}
.stick-benefits .benefit-big{font-size:9px}
.stick-brand{position:absolute;right:0;top:0;width:56px;height:100%;background:var(--brand-blue);display:flex;justify-content:center;align-items:center;gap:2px}
.stick-brand-name{writing-mode:vertical-rl;font-family:'Poppins',sans-serif;font-weight:800;color:var(--brand-yellow);font-size:12px;line-height:.95;white-space:nowrap}
.stick-brand-since{writing-mode:vertical-rl;font-family:'Poppins',sans-serif;font-weight:600;color:var(--white);font-size:3.5px}
</style>
</head>
<body>
<main class="canvas">

<!-- reusable icon set -->
<svg width="0" height="0" style="position:absolute" aria-hidden="true">
  <defs>
    <symbol id="icon-capsule" viewBox="0 0 20 24"><g fill="none" stroke="currentColor" stroke-width="1.8"><rect x="2" y="2" width="8" height="11" rx="4" transform="rotate(-30 6 7)"/><rect x="2" y="12" width="8" height="11" rx="4" transform="rotate(30 6 17)"/><circle cx="15" cy="8" r="2.2"/><circle cx="17" cy="14" r="1.6"/></g></symbol>
    <symbol id="icon-bolt" viewBox="0 0 14 24"><path d="M9 0 L1 13 H6 L3 24 L13 9 H8 Z" fill="currentColor"/></symbol>
    <symbol id="icon-helix" viewBox="0 0 24 24"><g fill="none" stroke="currentColor" stroke-width="1.8"><path d="M2 22 C8 22 8 14 12 12 C16 10 16 2 22 2"/><path d="M2 16 C6 10 12 18 16 10 C18 6 20 6 22 8"/><path d="M6 19 L8 15 M10 15 L12 12 M14 10 L16 6"/></g></symbol>
    <symbol id="icon-glass" viewBox="0 0 20 44"><g fill="none" stroke="#fff" stroke-width="1.6"><path d="M8 13 L18 1 L20 3 L10 15 Z"/><path d="M9 17 v1 M8 20 v1 M10 20 v1"/></g><path d="M2 22 H18 L16 43 H4 Z" fill="#fff"/></symbol>
  </defs>
</svg>

<!-- Lemon carton -->
<section class="carton flavor-lemon" style="left:76px">
  <svg class="carton-sky" width="327" height="160" aria-hidden="true"><polygon points="0,0 327,0 327,77 0,155" fill="var(--brand-blue)"/></svg>
  <div class="brand">vanta<br>prime</div>
  <div class="brand-since">Since 1992</div>
  <div class="portion"><div class="portion-main">20g x 20</div><div class="portion-sub">NET WT 0.7oz / 20g</div></div>
  <svg class="glass-icon" width="20" height="44" aria-hidden="true"><use href="#icon-glass"/></svg>
  <div class="count-badge"><span class="count-num">20</span><span class="count-label">STICKS</span></div>
  <h2 class="headline">HYDRATION BOOSTER</h2>
  <p class="tagline">REFRESH, REPLENISH &amp; RECHARGE!</p>
  <p class="descriptor">PREMIUM ISOTONIC ELECTROLYTE DRINK</p>
  <div class="benefits">
    <div class="benefit"><span class="benefit-big">5X</span><span>ELECTROLYTES</span></div>
    <div class="benefit"><svg width="18" height="22"><use href="#icon-capsule"/></svg><span>VITAMINS<br>&amp; MINERALS</span></div>
    <div class="benefit"><svg width="14" height="24"><use href="#icon-bolt"/></svg><span>FAST<br>HYDRATION</span></div>
    <div class="benefit"><svg width="20" height="20"><use href="#icon-helix"/></svg><span>NON GMO</span></div>
  </div>
  <div class="fruit-visual" role="img" aria-label="Photo of whole and halved lemons with leaves"></div>
  <svg class="flavor-band" width="327" height="26" aria-hidden="true"><path d="M0 20 H192 C200 20 205 2 214 2 H327 V26 H0 Z" fill="var(--accent)"/></svg>
  <div class="flavor-name">LEMON</div>
  <div class="footer-band"><span>NET WT 14.1oz / 400g</span><span>NUTRITIONAL EXPERTISE SINCE 1992</span></div>
</section>

<!-- Blackcurrant carton -->
<section class="carton flavor-currant" style="left:436px">
  <svg class="carton-sky" width="327" height="160" aria-hidden="true"><polygon points="0,0 327,0 327,77 0,155" fill="var(--brand-blue)"/></svg>
  <div class="brand">vanta<br>prime</div>
  <div class="brand-since">Since 1992</div>
  <div class="portion"><div class="portion-main">20g x 20</div><div class="portion-sub">NET WT 0.7oz / 20g</div></div>
  <svg class="glass-icon" width="20" height="44" aria-hidden="true"><use href="#icon-glass"/></svg>
  <div class="count-badge"><span class="count-num">20</span><span class="count-label">STICKS</span></div>
  <h2 class="headline">HYDRATION BOOSTER</h2>
  <p class="tagline">REFRESH, REPLENISH &amp; RECHARGE!</p>
  <p class="descriptor">PREMIUM ISOTONIC ELECTROLYTE DRINK</p>
  <div class="benefits">
    <div class="benefit"><span class="benefit-big">5X</span><span>ELECTROLYTES</span></div>
    <div class="benefit"><svg width="18" height="22"><use href="#icon-capsule"/></svg><span>VITAMINS<br>&amp; MINERALS</span></div>
    <div class="benefit"><svg width="14" height="24"><use href="#icon-bolt"/></svg><span>FAST<br>HYDRATION</span></div>
    <div class="benefit"><svg width="20" height="20"><use href="#icon-helix"/></svg><span>NON GMO</span></div>
  </div>
  <div class="fruit-visual" role="img" aria-label="Photo of a cluster of blackcurrants with leaves"></div>
  <svg class="flavor-band" width="327" height="26" aria-hidden="true"><path d="M0 20 H192 C200 20 205 2 214 2 H327 V26 H0 Z" fill="var(--accent)"/></svg>
  <div class="flavor-name">BLACKCURRANT</div>
  <div class="footer-band"><span>NET WT 14.1oz / 400g</span><span>NUTRITIONAL EXPERTISE SINCE 1992</span></div>
</section>

<!-- Orange carton -->
<section class="carton flavor-orange" style="left:797px">
  <svg class="carton-sky" width="327" height="160" aria-hidden="true"><polygon points="0,0 327,0 327,77 0,155" fill="var(--brand-blue)"/></svg>
  <div class="brand">vanta<br>prime</div>
  <div class="brand-since">Since 1992</div>
  <div class="portion"><div class="portion-main">20g x 20</div><div class="portion-sub">NET WT 0.7oz / 20g</div></div>
  <svg class="glass-icon" width="20" height="44" aria-hidden="true"><use href="#icon-glass"/></svg>
  <div class="count-badge"><span class="count-num">20</span><span class="count-label">STICKS</span></div>
  <h2 class="headline">HYDRATION BOOSTER</h2>
  <p class="tagline">REFRESH, REPLENISH &amp; RECHARGE!</p>
  <p class="descriptor">PREMIUM ISOTONIC ELECTROLYTE DRINK</p>
  <div class="benefits">
    <div class="benefit"><span class="benefit-big">5X</span><span>ELECTROLYTES</span></div>
    <div class="benefit"><svg width="18" height="22"><use href="#icon-capsule"/></svg><span>VITAMINS<br>&amp; MINERALS</span></div>
    <div class="benefit"><svg width="14" height="24"><use href="#icon-bolt"/></svg><span>FAST<br>HYDRATION</span></div>
    <div class="benefit"><svg width="20" height="20"><use href="#icon-helix"/></svg><span>NON GMO</span></div>
  </div>
  <div class="fruit-visual" role="img" aria-label="Photo of whole and halved oranges with leaves"></div>
  <svg class="flavor-band" width="327" height="26" aria-hidden="true"><path d="M0 20 H192 C200 20 205 2 214 2 H327 V26 H0 Z" fill="var(--accent)"/></svg>
  <div class="flavor-name">ORANGE</div>
  <div class="footer-band"><span>NET WT 14.1oz / 400g</span><span>NUTRITIONAL EXPERTISE SINCE 1992</span></div>
</section>

<!-- Sticks -->
<section class="stick flavor-lemon" style="left:100px">
  <div class="stick-edge"><span class="stick-weight">NET WT 0.7oz / 20g</span><span class="stick-flavor">LEMON</span></div>
  <div class="stick-fruit" role="img" aria-label="Photo of halved lemon with leaves"></div>
  <h3 class="stick-headline">HYDRATION BOOSTER</h3>
  <p class="stick-descriptor">PREMIUM ISOTONIC ELECTROLYTE DRINK</p>
  <div class="stick-benefits">
    <div class="benefit"><span class="benefit-big">5X</span><span>ELECTROLYTES</span></div>
    <div class="benefit"><svg width="9" height="11"><use href="#icon-capsule"/></svg><span>VITAMINS<br>&amp; MINERALS</span></div>
    <div class="benefit"><svg width="6" height="11"><use href="#icon-bolt"/></svg><span>FAST<br>HYDRATION</span></div>
    <div class="benefit"><svg width="10" height="10"><use href="#icon-helix"/></svg><span>NON GMO</span></div>
  </div>
  <div class="stick-brand"><span class="stick-brand-since">Since 1992</span><span class="stick-brand-name">vanta<br>prime</span></div>
</section>

<section class="stick flavor-currant" style="left:461px">
  <div class="stick-edge"><span class="stick-weight">NET WT 0.7oz / 20g</span><span class="stick-flavor">BLACKCURRANT</span></div>
  <div class="stick-fruit" role="img" aria-label="Photo of blackcurrant cluster with leaves"></div>
  <h3 class="stick-headline">HYDRATION BOOSTER</h3>
  <p class="stick-descriptor">PREMIUM ISOTONIC ELECTROLYTE DRINK</p>
  <div class="stick-benefits">
    <div class="benefit"><span class="benefit-big">5X</span><span>ELECTROLYTES</span></div>
    <div class="benefit"><svg width="9" height="11"><use href="#icon-capsule"/></svg><span>VITAMINS<br>&amp; MINERALS</span></div>
    <div class="benefit"><svg width="6" height="11"><use href="#icon-bolt"/></svg><span>FAST<br>HYDRATION</span></div>
    <div class="benefit"><svg width="10" height="10"><use href="#icon-helix"/></svg><span>NON GMO</span></div>
  </div>
  <div class="stick-brand"><span class="stick-brand-since">Since 1992</span><span class="stick-brand-name">vanta<br>prime</span></div>
</section>

<section class="stick flavor-orange" style="left:821px">
  <div class="stick-edge"><span class="stick-weight">NET WT 0.7oz / 20g</span><span class="stick-flavor">LEMON</span></div>
  <div class="stick-fruit" role="img" aria-label="Photo of whole and halved oranges"></div>
  <h3 class="stick-headline">HYDRATION BOOSTER</h3>
  <p class="stick-descriptor">PREMIUM ISOTONIC ELECTROLYTE DRINK</p>
  <div class="stick-benefits">
    <div class="benefit"><span class="benefit-big">5X</span><span>ELECTROLYTES</span></div>
    <div class="benefit"><svg width="9" height="11"><use href="#icon-capsule"/></svg><span>VITAMINS<br>&amp; MINERALS</span></div>
    <div class="benefit"><svg width="6" height="11"><use href="#icon-bolt"/></svg><span>FAST<br>HYDRATION</span></div>
    <div class="benefit"><svg width="10" height="10"><use href="#icon-helix"/></svg><span>NON GMO</span></div>
  </div>
  <div class="stick-brand"><span class="stick-brand-since">Since 1992</span><span class="stick-brand-name">vanta<br>prime</span></div>
</section>

</main>
</body>
</html>
```